BRIGHT CORAL INC , CELL PHONE STORE

We need website design . we already have one but not happy with it www.brightcoralinc.example
we cell phones provide service ,phone repair ,
phone accessories.
online sale payment via PayVerra
shipping by QDMX

Industry/Entity Type

Cell Phone

Number of Pages Required

5+ page

Font styles to use
Serif
Sans Serif

Colors
3176b5

Requirements
Must have
• online sale via PayVerra
Nice to have
• email address

```html
<!DOCTYPE html>
<html lang="en">
<head>
<meta charset="utf-8">
<title>Bright Coral Inc — Cell Phone Store</title>
<link href="https://fonts.googleapis.com/css2?family=Montserrat:wght@400;500;600;700&display=swap" rel="stylesheet">
<style>
:root{
  --brand:#3176b5;
  --brand-dark:#265f94;
  --coral:#d9392f;
  --ink:#333a40;
  --muted:#6b7178;
  --line:#e6e8ea;
  --footer:#f8f8f8;
  --white:#ffffff;
}
*{box-sizing:border-box;margin:0;padding:0}
html,body{width:1200px;height:2179px;overflow:hidden}
body{position:relative;background:var(--white);font-family:"Montserrat",Arial,sans-serif;color:var(--ink)}
.abs{position:absolute}
a{color:inherit;text-decoration:none}

.topbar{left:0;top:0;width:1200px;height:41px;background:var(--brand);color:var(--white);font-size:11px}
.topbar .contact{left:141px;top:14px;display:flex;gap:22px;align-items:center}
.topbar .account{right:141px;top:14px;display:flex;gap:14px;align-items:center}
.topbar span{display:inline-flex;align-items:center;gap:7px}
.topbar svg{width:11px;height:11px;fill:var(--white)}

.header{left:0;top:41px;width:1200px;height:101px}
.logo{font-weight:600;color:var(--coral);font-size:19px;letter-spacing:.2px;display:flex;align-items:center;gap:7px;white-space:nowrap}
.logo i{display:block;width:7px;height:7px;border-radius:50%;background:var(--coral)}
.header .logo{left:141px;top:39px}
.search{left:388px;top:30px;width:453px;height:45px;border:1px solid var(--line);border-radius:3px;display:flex;align-items:center;padding-left:16px;font-size:11px;color:var(--ink)}
.search button{position:absolute;right:4px;top:5px;width:42px;height:33px;border:0;border-radius:3px;background:var(--brand);display:flex;align-items:center;justify-content:center}
.menu-label{left:966px;top:47px;font-size:11px;font-weight:500}
.menu-btn{left:1012px;top:35px;width:44px;height:36px;border:1px solid #cfd3d6;border-radius:3px;display:flex;flex-direction:column;justify-content:center;align-items:center;gap:3px}
.menu-btn b{display:block;width:12px;height:2px;background:var(--brand)}

.hero{left:0;top:142px;width:1200px;height:429px;background:linear-gradient(100deg,#4b4a52 0%,#8a6a4d 22%,#6b6e78 45%,#3e5663 70%,#2c4150 100%)}
.hero-copy{left:176px;top:118px;color:var(--white)}
.hero-copy h1{font-size:38px;font-weight:700;line-height:42px;letter-spacing:.3px}
.hero-copy p{margin-top:12px;font-size:19px;line-height:26px;font-weight:400;width:290px}
.btn{display:inline-flex;align-items:center;justify-content:center;background:var(--brand);color:var(--white);font-size:11px;font-weight:500;border-radius:3px;letter-spacing:.3px}
.hero-copy .btn{margin-top:24px;width:111px;height:33px}
.dots{left:1148px;top:343px;display:flex;flex-direction:column;gap:7px}
.dots i{display:block;width:6px;height:6px;border-radius:50%;background:rgba(255,255,255,.85)}
.dots i.on{background:var(--brand)}

.brands{left:0;top:628px;width:1200px;display:flex;justify-content:center;gap:78px;font-size:16px;font-weight:600;color:#555c63}

.tabs{left:0;top:748px;width:1200px;display:flex;justify-content:center;align-items:center;gap:22px;font-size:24px;color:var(--ink)}
.tabs .active{color:var(--brand)}
.tabs .sep{font-size:22px}
.tab-line{left:424px;top:796px;width:57px;height:3px;background:var(--ink)}

.grid{left:141px;top:847px;width:912px;display:grid;grid-template-columns:repeat(3,289px);column-gap:23px;row-gap:24px}
.card{height:397px;border:1px solid var(--line);border-radius:2px;text-align:center;position:relative}
.card .thumb{position:absolute;left:10px;top:14px;width:267px;height:222px;border-radius:3px}
.card h3{position:absolute;left:0;right:0;top:250px;font-size:14px;font-weight:500;color:var(--brand)}
.card .price{position:absolute;left:0;right:0;top:280px;font-size:29px;font-weight:400;color:#555}
.card .btn{position:absolute;left:81px;top:339px;width:118px;height:34px;font-size:10px}
.t-case{background:linear-gradient(180deg,#f7f7f7,#e7e7e7)}
.t-phone{background:linear-gradient(180deg,#fafafa,#ececec)}
.t-smart{background:linear-gradient(160deg,#eef3f9,#b9d3f0)}
.t-head{background:linear-gradient(160deg,#f2f2f2,#b9b9b9)}
.t-ear{background:linear-gradient(160deg,#f0f0f0,#8e8e8e)}
.t-spk{background:linear-gradient(180deg,#f8f1ef,#ecc3b9)}

.more{left:481px;top:1710px;width:239px;height:51px;border:1px solid #b9bec3;border-radius:3px;display:flex;align-items:center;justify-content:center;font-size:13px;font-weight:500;color:var(--brand)}

.footer{left:0;top:1839px;width:1200px;height:261px;background:var(--footer)}
.footer .logo{left:141px;top:60px}
.fcol{top:60px}
.fcol h4{font-size:14px;font-weight:600;color:var(--brand);margin-bottom:28px}
.fcol li{list-style:none;font-size:14px;color:var(--muted);line-height:25.5px}
.bottom{left:0;top:2100px;width:1200px;height:79px;border-top:1px solid var(--line);background:var(--white)}
.copy{left:141px;top:32px;font-size:13px;font-weight:500;color:var(--ink)}
.ship{left:600px;top:31px;display:flex;align-items:center;gap:10px;font-size:10px;font-weight:600;color:var(--ink)}
.ship i{display:block;width:12px;height:12px;background:var(--brand)}
.pay{left:826px;top:30px;display:flex;gap:7px}
.pay span{width:42px;height:22px;border:1px solid var(--line);border-radius:2px;font-size:7px;font-weight:600;color:#2a4a8a;display:flex;align-items:center;justify-content:center;background:var(--white)}
</style>
</head>
<body>

<div class="abs topbar">
  <div class="abs contact">
    <span><svg viewBox="0 0 24 24"><path d="M6.6 10.8a15 15 0 0 0 6.6 6.6l2.2-2.2c.3-.3.7-.4 1-.2 1.1.4 2.3.6 3.6.6.6 0 1 .4 1 1V20c0 .6-.4 1-1 1A17 17 0 0 1 3 4c0-.6.4-1 1-1h3.5c.6 0 1 .4 1 1 0 1.3.2 2.5.6 3.6.1.3 0 .7-.2 1z"/></svg>1 555 010 2468 &nbsp;|</span>
    <span><svg viewBox="0 0 24 24"><path d="M2 5h20v14H2zm2 2v.5l8 5 8-5V7zm0 2.8V17h16V9.8l-8 5z"/></svg>hello@brightcoralinc.example</span>
  </div>
  <div class="abs account">
    <span><svg viewBox="0 0 24 24"><path d="M3 17.2V21h3.8L18 9.8 14.2 6zM20.7 7.1a1 1 0 0 0 0-1.4l-2.4-2.4a1 1 0 0 0-1.4 0L15 5.2 18.8 9z"/></svg>Register &nbsp;|</span>
    <span><svg viewBox="0 0 24 24"><path d="M6 10V8a6 6 0 0 1 12 0v2h1v12H5V10zm2 0h8V8a4 4 0 0 0-8 0z"/></svg>Login</span>
  </div>
</div>

<header class="abs header">
  <div class="abs logo">BRIGHT CORAL INC<i></i></div>
  <div class="abs search">Search
    <button aria-label="Search"><svg width="14" height="14" viewBox="0 0 24 24" fill="none" stroke="#fff" stroke-width="3"><circle cx="10" cy="10" r="6"/><path d="M15 15l6 6"/></svg></button>
  </div>
  <div class="abs menu-label">MENU</div>
  <div class="abs menu-btn"><b></b><b></b><b></b></div>
</header>

<section class="abs hero" role="img" aria-label="Blurred city street with a hand holding a smartphone">
  <div class="abs hero-copy">
    <h1>WE CAN<br>COME TO YOU</h1>
    <p>Fix your phone in your home or at your work</p>
    <a class="btn" href="#">LEARN MORE</a>
  </div>
  <div class="abs dots"><i></i><i></i><i></i><i class="on"></i></div>
</section>

<div class="abs brands">
  <span>Tellmo</span><span>Ultrava</span><span>Netora</span><span>Sumvio</span><span>Pomely</span>
</div>

<nav class="abs tabs">
  <span class="active">Featured</span><span class="sep">|</span><span>New Arrivals</span><span class="sep">|</span><span>Best Sellers</span>
</nav>
<div class="abs tab-line"></div>

<section class="abs grid">
  <article class="card"><div class="thumb t-case" role="img" aria-label="Product photo: white phone back cover"></div><h3>Pocketa Back Cover</h3><div class="price">$28.00</div><a class="btn" href="#">ADD TO CART</a></article>
  <article class="card"><div class="thumb t-phone" role="img" aria-label="Product photo: white smartphone, front view"></div><h3>Pocketa Back Cover</h3><div class="price">$28.00</div><a class="btn" href="#">ADD TO CART</a></article>
  <article class="card"><div class="thumb t-smart" role="img" aria-label="Product photo: smartphone with blue screen"></div><h3>Pocketa Back Cover</h3><div class="price">$28.00</div><a class="btn" href="#">ADD TO CART</a></article>
  <article class="card"><div class="thumb t-head" role="img" aria-label="Product photo: white and black over-ear headphones"></div><h3>Pocketa Back Cover</h3><div class="price">$28.00</div><a class="btn" href="#">ADD TO CART</a></article>
  <article class="card"><div class="thumb t-ear" role="img" aria-label="Product photo: black wireless earpiece"></div><h3>Pocketa Back Cover</h3><div class="price">$28.00</div><a class="btn" href="#">ADD TO CART</a></article>
  <article class="card"><div class="thumb t-spk" role="img" aria-label="Product photo: red and white portable speaker"></div><h3>Pocketa Back Cover</h3><div class="price">$28.00</div><a class="btn" href="#">ADD TO CART</a></article>
</section>

<a class="abs more" href="#">VIEW MORE PRODUCTS</a>

<footer class="abs footer">
  <div class="abs logo">BRIGHT CORAL INC<i></i></div>
  <div class="abs fcol" style="left:424px"><h4>Customer Service</h4><ul><li>Contact Us</li><li>Privacy Policy</li><li>Terms &amp; Conditions</li></ul></div>
  <div class="abs fcol" style="left:652px"><h4>Quick Links</h4><ul><li>Login</li><li>New Customers</li><li>Products</li><li>Phone Repair</li></ul></div>
  <div class="abs fcol" style="left:840px"><h4>Information</h4><ul><li>Home</li><li>About Us</li></ul></div>
</footer>

<div class="abs bottom">
  <div class="abs copy">© Bright Coral Inc - All Rights Reserved</div>
  <div class="abs ship"><i></i>QDMX SHIPPING</div>
  <div class="abs pay"><span>PayVerra</span><span>Cardlo</span><span>Mintcard</span><span>Vantis</span><span>Dovera</span></div>
</div>

</body>
</html>
```